Retail Sign for Houseplant Campaign

Sign will measure 3 to 4 foot tall by 22.2inches and place on rolling racks of houseplants for a retail promotion in The Birchwell Yard. The theme of the promotion will be "New Year, New You!" Selling points which should be on the sign are Houseplants give you a taste of nature, Houseplants boost air quality inside your home, Indoor plants reduce anxiety, Indoor plants make you more productive, Houseplants improve your concentration and memory.
Updates

Target Market(s)

People who love plants

Industry/Entity Type

Horticulture/ retail

Colors
00AB8E
00BBA5
67D7C9
C6EFE9
E9F9F6
59FF00
82FF00
B8FF75
E3FFCB
F4FFEA
FFF300
FFF600
FEFA6F
FFFEC7
FFFEE8

Requirements
Must have
• Must feel energetic and encourage people to buy plants. Should include 1-2 photos and the selling points listed

```html
<!DOCTYPE html>
<html lang="en">
<head>
<meta charset="utf-8">
<title>New Year, New You! – Houseplant Sign</title>
<link rel="stylesheet" href="https://fonts.googleapis.com/css2?family=Andika&family=Kaushan+Script&display=swap">
<style>
  :root {
    --page: #ffffff;
    --ink: #262626;
    --teal: #6fdbc8;
    --mint: #9fe3b6;
    --lime: #e2f68a;
    --leaf-faint: #5fc3a3;
    --photo-light: #e4ebe2;
    --photo-soft: #b9d2b0;
    --photo-leaf: #4f8f4a;
    --photo-deep: #1f5a2a;
  }
  * { margin: 0; padding: 0; box-sizing: border-box; }
  html, body {
    width: 668px; height: 1200px; overflow: hidden; background: var(--page);
  }
  .sign {
    position: absolute;
    left: 96px; top: 88px;
    width: 466px; height: 1005px;
    overflow: hidden;
    background: linear-gradient(155deg, var(--teal) 0%, var(--mint) 45%, var(--lime) 85%);
  }
  .leaf-decor {
    position: absolute;
    background: var(--leaf-faint);
    opacity: 0.5;
    border-radius: 50%;
  }
  .leaf-decor--left { left: -40px; top: -30px; width: 220px; height: 200px; transform: rotate(-20deg); }
  .leaf-decor--right { right: -40px; top: -10px; width: 120px; height: 105px; transform: rotate(25deg); }
  .brand {
    position: absolute;
    left: 0; right: 0; top: 62px;
    display: flex; align-items: center; justify-content: center; gap: 10px;
    font-family: "Andika", sans-serif;
    font-weight: 400;
    color: var(--ink);
    font-size: 28px;
    letter-spacing: 0.5px;
  }
  .brand__mark { width: 40px; height: 40px; background: var(--ink); }
  .headline {
    position: absolute;
    left: 0; right: 0; top: 128px;
    text-align: center;
    font-family: "Kaushan Script", cursive;
    font-weight: 400;
    font-size: 60px;
    line-height: 66px;
    color: var(--ink);
  }
  .points {
    position: absolute;
    left: 40px; right: 40px; top: 278px;
    list-style: none;
    text-align: center;
    font-family: "Andika", sans-serif;
    font-size: 20px;
    line-height: 29px;
    color: var(--ink);
  }
  .points li { margin-bottom: 10px; }
  .photo { position: absolute; left: 0; top: 0; width: 466px; height: 1005px; }
</style>
</head>
<body>
  <main class="sign">
    <div class="leaf-decor leaf-decor--left" role="img" aria-label="Faint monstera leaf decoration"></div>
    <div class="leaf-decor leaf-decor--right" role="img" aria-label="Faint monstera leaf decoration"></div>

    <div class="brand">
      <span class="brand__mark"></span>
      <span class="brand__name">Greenleaf Makers</span>
    </div>

    <h1 class="headline">New Year,<br>New You!</h1>

    <ul class="points">
      <li>Houseplants give you a<br>taste of nature</li>
      <li>Houseplants boost air quality<br>inside your home</li>
      <li>Indoor plants reduce anxiety</li>
      <li>Indoor plants make you<br>more productive</li>
      <li>Houseplants improve your<br>concentration and memory</li>
    </ul>

    <svg class="photo" viewBox="0 0 466 1005" role="img" aria-label="Photo of a smiling woman wiping the leaves of a large monstera plant in a bright room">
      <defs>
        <linearGradient id="photoTone" x1="0" y1="0.2" x2="1" y2="0.9">
          <stop offset="0" stop-color="var(--photo-light)"/>
          <stop offset="0.4" stop-color="var(--photo-soft)"/>
          <stop offset="0.75" stop-color="var(--photo-leaf)"/>
          <stop offset="1" stop-color="var(--photo-deep)"/>
        </linearGradient>
      </defs>
      <path d="M0 650 C40 640 90 615 150 600 C200 588 240 586 275 590 C305 594 325 602 344 606 C390 600 430 590 466 568 L466 1005 L0 1005 Z" fill="url(#photoTone)"/>
    </svg>
  </main>
</body>
</html>
```